Packaging Design for Vanta Prime

We require an outstanding packaging design for our Vanta Prime brand, which offers hydration electrolyte supplements specifically tailored for athletes and sporty individuals.

Benchmark packaging design from quellix competitor attached. The product packaging contains 20 x 20g sticks of the product.

Target Market

Psychographic: Health-conscious, active lifestyle, values quality, functionality and sustainability.

product description 1:
HYDRATION BOOSTER
Refresh, Replenish, Recharge!

product description 2:
PREMIUM ISOTONIC ELECTROLYTE DRINK
Nutritional Expertise Since 1992.

Existing Logo: to add "since 1992"

Appeal to Target Market: Create a design that resonates with both men and women in the 25-55 age group.

Grafik Design: Develop a visually striking design that grabs attention in online retail environments like Brindleport.

Visuals: glass of water (or symbolic) and sticks (powder) just like benchmark brand quellix.

Design Elements
Use colours that are inside the Vanta-Prime Logo, attached.
Product will be available in 3 flavours. Lemon=yellow, Orange=orange, Black Currant=purple

Typography: Utilize strong, clean, and modern fonts. Ensure readability and create a sense of strength, endurance and reliability.

The product will be available in 3 flavours: Lemon, Orange and Johannisbeere

We look forward to seeing your creative ideas and innovative designs for our Vanta Prime brand packaging.

```html
<!DOCTYPE html>
<html lang="en">
<head>
<meta charset="utf-8">
<title>Vanta Prime Hydration Booster – Packaging</title>
<link rel="stylesheet" href="https://fonts.googleapis.com/css2?family=Roboto+Condensed:ital,wght@0,400;0,700;0,800;1,800&display=swap">
<style>
  :root {
    --pouch-blue: #1f4fb3;
    --pouch-blue-deep: #173f99;
    --brand-yellow: #f2dc1b;
    --brand-pink: #c9195b;
    --white: #ffffff;
    --badge-green: #2f8a3a;
    --purple: #4b1a8c;
    --purple-light: #c9a6ee;
    --yellow: #e8d21e;
    --yellow-light: #fbf3a8;
    --orange: #ec6a12;
    --orange-light: #fbb486;
  }
  * { box-sizing: border-box; margin: 0; padding: 0; }
  html, body { width: 1200px; height: 600px; overflow: hidden; }
  body { font-family: "Roboto Condensed", "Arial Narrow", sans-serif; display: flex; }

  .flavor-panel {
    position: relative;
    width: 400px;
    height: 600px;
    background: radial-gradient(ellipse 60% 45% at 50% 10%, var(--glow) 0%, var(--flavor) 100%);
  }
  .flavor-panel--currant { --flavor: var(--purple); --flavor-deep: #3e1475; --glow: var(--purple-light); --band-text: var(--white); --label-text: var(--white); --sub-text: var(--brand-yellow); }
  .flavor-panel--lemon   { --flavor: var(--yellow); --flavor-deep: #dcc512; --glow: var(--yellow-light); --band-text: #10183a; --label-text: var(--white); --sub-text: var(--pouch-blue-deep); }
  .flavor-panel--orange  { --flavor: var(--orange); --flavor-deep: #e05e0a; --glow: var(--orange-light); --band-text: #fff3dc; --label-text: var(--white); --sub-text: var(--brand-yellow); }

  .pouch {
    position: absolute;
    left: 35px; top: 88px;
    width: 330px; height: 428px;
    background: var(--pouch-blue);
    overflow: hidden;
    box-shadow: 0 10px 24px rgba(0,0,0,.22);
  }
  .pouch__top-band {
    position: absolute; left: 0; top: 0; width: 100%; height: 38px;
    background: var(--flavor-deep);
    color: var(--band-text);
    font-size: 13px; text-align: center; line-height: 40px;
  }
  .pouch__bottom { position: absolute; left: 0; top: 0; width: 330px; height: 428px; }

  .suitability { position: absolute; left: 4px; width: 48px; text-align: center; color: var(--white); }
  .suitability--pregnancy { top: 60px; }
  .suitability--nursing { top: 112px; }
  .suitability--kids { top: 166px; }
  .suitability__icon { display: block; margin: 0 auto 3px; }
  .suitability__label { font-size: 4.2px; line-height: 5px; text-transform: uppercase; }

  .brand-name {
    position: absolute; left: 95px; top: 78px;
    display: flex; align-items: center; gap: 7px;
    color: var(--brand-yellow);
    font-size: 30px; font-weight: 800;
  }
  .brand-name__dot { width: 20px; height: 20px; border-radius: 50%; background: var(--brand-pink); }

  .certification-badge {
    position: absolute; left: 274px; top: 50px;
    width: 36px; height: 28px; background: var(--badge-green); border-radius: 2px;
  }

  .product-title {
    position: absolute; left: 58px; top: 158px;
    font-size: 27px; font-weight: 700; color: var(--white); white-space: nowrap; letter-spacing: -.2px;
  }
  .product-title__accent { color: var(--brand-yellow); font-style: italic; font-weight: 800; }

  .product-subtitle {
    position: absolute; left: 60px; top: 205px; width: 214px; text-align: center;
    font-size: 12.5px; color: var(--white); white-space: nowrap;
  }

  .claim-ribbon {
    position: absolute; left: 77px; top: 231px; width: 179px; height: 19px;
    background: var(--brand-pink); transform: skewX(-12deg);
  }
  .claim-ribbon__text {
    position: absolute; left: 77px; top: 231px; width: 179px; height: 19px;
    color: var(--white); font-size: 9.5px; font-weight: 700; line-height: 19px; text-align: center; word-spacing: 1px;
  }

  .fruit-illustration {
    position: absolute; left: 28px; top: 250px; width: 74px; height: 78px; border-radius: 50%;
    background: radial-gradient(circle at 40% 35%, var(--fruit-a), var(--fruit-b));
  }
  .flavor-panel--currant .fruit-illustration { --fruit-a: #3d3550; --fruit-b: #120e1a; }
  .flavor-panel--lemon   .fruit-illustration { --fruit-a: #fff27a; --fruit-b: #e3c313; }
  .flavor-panel--orange  .fruit-illustration { --fruit-a: #ffb04a; --fruit-b: #e86a0c; }

  .stick-count {
    position: absolute; left: 151px; top: 273px; width: 43px; height: 49px; border-radius: 50%;
    border: 1.3px solid var(--white); color: var(--white); text-align: center;
  }
  .stick-count__number { display: block; font-size: 22px; font-weight: 700; line-height: 26px; margin-top: 3px; }
  .stick-count__unit { display: block; font-size: 7.5px; font-weight: 700; }

  .serving-illustration {
    position: absolute; left: 224px; top: 285px; width: 86px; height: 80px;
    background: linear-gradient(160deg, rgba(255,255,255,.08) 0%, rgba(255,255,255,.16) 45%, var(--flavor) 100%);
    border-radius: 3px;
  }
  .stick-illustration {
    position: absolute; left: 270px; top: 258px; width: 46px; height: 14px;
    background: var(--pouch-blue-deep); transform: rotate(-32deg);
  }

  .flavor-name {
    position: absolute; left: 19px; top: 331px;
    color: var(--label-text); font-size: 15px; font-weight: 700; line-height: 17px;
  }
  .flavor-name__note { display: block; margin-left: 23px; font-size: 9px; line-height: 12px; font-weight: 400; color: var(--sub-text); }

  .free-from {
    position: absolute; left: 78px; top: 368px; width: 210px; text-align: center; white-space: nowrap;
    color: var(--band-text); font-size: 9px;
  }
  .diet-marks { position: absolute; left: 119px; top: 386px; display: flex; gap: 17px; }
  .diet-mark { width: 20px; text-align: center; color: var(--band-text); }
  .diet-mark__icon { width: 19px; height: 19px; border: 1.2px solid var(--band-text); border-radius: 50%; margin: 0 auto 3px; }
  .diet-mark__label { font-size: 3.8px; text-transform: uppercase; }
  .net-weight {
    position: absolute; left: 78px; top: 415px; width: 210px; text-align: center;
    color: var(--band-text); font-size: 6.5px;
  }
</style>
</head>
<body>

<section class="flavor-panel flavor-panel--currant">
  <article class="pouch">
    <svg class="pouch__bottom" viewBox="0 0 330 428" aria-hidden="true">
      <path d="M0 326 L142 326 Q152 326 160 336 L180 360 L330 360 L330 428 L0 428 Z" fill="var(--flavor)"/>
    </svg>
    <div class="pouch__top-band">NUTRITIONAL EXPERTISE SINCE 1992</div>
    <div class="suitability suitability--pregnancy"><svg class="suitability__icon" width="22" height="22" viewBox="0 0 22 22"><circle cx="11" cy="11" r="9.5" fill="none" stroke="#fff" stroke-width="1.3"/></svg><p class="suitability__label">Für Schwangere geeignet</p></div>
    <div class="suitability suitability--nursing"><svg class="suitability__icon" width="22" height="26" viewBox="0 0 22 26"><rect x="5" y="2" width="12" height="22" rx="6" fill="none" stroke="#fff" stroke-width="1.3"/></svg><p class="suitability__label">Für Stillende geeignet</p></div>
    <div class="suitability suitability--kids"><svg class="suitability__icon" width="24" height="24" viewBox="0 0 24 24"><circle cx="7" cy="12" r="5.5" fill="none" stroke="#fff" stroke-width="1.3"/><circle cx="17" cy="12" r="5.5" fill="none" stroke="#fff" stroke-width="1.3"/></svg><p class="suitability__label">Für Kinder ab 4 Jahre</p></div>
    <div class="brand-name"><span class="brand-name__dot"></span>Vanta Prime</div>
    <div class="certification-badge"></div>
    <h1 class="product-title">HYDRATION <span class="product-title__accent">BOOSTER</span></h1>
    <p class="product-subtitle">PREMIUM ISOTONIC ELECTROLYTE DRINK</p>
    <div class="claim-ribbon"></div>
    <p class="claim-ribbon__text">• REFRESH • REPLENISH • RECHARGE!</p>
    <div class="fruit-illustration" role="img" aria-label="Black currant berries with leaves"></div>
    <div class="stick-count"><span class="stick-count__number">20</span><span class="stick-count__unit">STICKS</span></div>
    <div class="stick-illustration" role="img" aria-label="Product stick tilted over the glass"></div>
    <div class="serving-illustration" role="img" aria-label="Purple powder pouring into a glass of water"></div>
    <p class="flavor-name">BLACK CURRANT FLAVOR<span class="flavor-name__note">NATURAL FLAVOR</span></p>
    <p class="free-from">NO ARTIFICIAL COLORS, FLAVORS, OR SWEETENERS</p>
    <div class="diet-marks">
      <div class="diet-mark"><div class="diet-mark__icon"></div><p class="diet-mark__label">Vegan</p></div>
      <div class="diet-mark"><div class="diet-mark__icon"></div><p class="diet-mark__label">Glutenfrei</p></div>
      <div class="diet-mark"><div class="diet-mark__icon"></div><p class="diet-mark__label">Laktosefrei</p></div>
    </div>
    <p class="net-weight">NET WT. 400G (14.11 Oz)</p>
  </article>
</section>

<section class="flavor-panel flavor-panel--lemon">
  <article class="pouch">
    <svg class="pouch__bottom" viewBox="0 0 330 428" aria-hidden="true">
      <path d="M0 326 L142 326 Q152 326 160 336 L180 360 L330 360 L330 428 L0 428 Z" fill="var(--flavor)"/>
    </svg>
    <div class="pouch__top-band">NUTRITIONAL EXPERTISE SINCE 1992</div>
    <div class="suitability suitability--pregnancy"><svg class="suitability__icon" width="22" height="22" viewBox="0 0 22 22"><circle cx="11" cy="11" r="9.5" fill="none" stroke="#fff" stroke-width="1.3"/></svg><p class="suitability__label">Für Schwangere geeignet</p></div>
    <div class="suitability suitability--nursing"><svg class="suitability__icon" width="22" height="26" viewBox="0 0 22 26"><rect x="5" y="2" width="12" height="22" rx="6" fill="none" stroke="#fff" stroke-width="1.3"/></svg><p class="suitability__label">Für Stillende geeignet</p></div>
    <div class="suitability suitability--kids"><svg class="suitability__icon" width="24" height="24" viewBox="0 0 24 24"><circle cx="7" cy="12" r="5.5" fill="none" stroke="#fff" stroke-width="1.3"/><circle cx="17" cy="12" r="5.5" fill="none" stroke="#fff" stroke-width="1.3"/></svg><p class="suitability__label">Für Kinder ab 4 Jahre</p></div>
    <div class="brand-name"><span class="brand-name__dot"></span>Vanta Prime</div>
    <div class="certification-badge"></div>
    <h1 class="product-title">HYDRATION <span class="product-title__accent">BOOSTER</span></h1>
    <p class="product-subtitle">PREMIUM ISOTONIC ELECTROLYTE DRINK</p>
    <div class="claim-ribbon"></div>
    <p class="claim-ribbon__text">• REFRESH • REPLENISH • RECHARGE!</p>
    <div class="fruit-illustration" role="img" aria-label="Whole and sliced lemons with leaves"></div>
    <div class="stick-count"><span class="stick-count__number">20</span><span class="stick-count__unit">STICKS</span></div>
    <div class="stick-illustration" role="img" aria-label="Product stick tilted over the glass"></div>
    <div class="serving-illustration" role="img" aria-label="Yellow powder pouring into a glass of water"></div>
    <p class="flavor-name">LEMON FLAVOR<span class="flavor-name__note">NATURAL FLAVOR</span></p>
    <p class="free-from">NO ARTIFICIAL COLORS, FLAVORS, OR SWEETENERS</p>
    <div class="diet-marks">
      <div class="diet-mark"><div class="diet-mark__icon"></div><p class="diet-mark__label">Vegan</p></div>
      <div class="diet-mark"><div class="diet-mark__icon"></div><p class="diet-mark__label">Glutenfrei</p></div>
      <div class="diet-mark"><div class="diet-mark__icon"></div><p class="diet-mark__label">Laktosefrei</p></div>
    </div>
    <p class="net-weight">NET WT. 400G (14.11 Oz)</p>
  </article>
</section>

<section class="flavor-panel flavor-panel--orange">
  <article class="pouch">
    <svg class="pouch__bottom" viewBox="0 0 330 428" aria-hidden="true">
      <path d="M0 326 L142 326 Q152 326 160 336 L180 360 L330 360 L330 428 L0 428 Z" fill="var(--flavor)"/>
    </svg>
    <div class="pouch__top-band">NUTRITIONAL EXPERTISE SINCE 1992</div>
    <div class="suitability suitability--pregnancy"><svg class="suitability__icon" width="22" height="22" viewBox="0 0 22 22"><circle cx="11" cy="11" r="9.5" fill="none" stroke="#fff" stroke-width="1.3"/></svg><p class="suitability__label">Für Schwangere geeignet</p></div>
    <div class="suitability suitability--nursing"><svg class="suitability__icon" width="22" height="26" viewBox="0 0 22 26"><rect x="5" y="2" width="12" height="22" rx="6" fill="none" stroke="#fff" stroke-width="1.3"/></svg><p class="suitability__label">Für Stillende geeignet</p></div>
    <div class="suitability suitability--kids"><svg class="suitability__icon" width="24" height="24" viewBox="0 0 24 24"><circle cx="7" cy="12" r="5.5" fill="none" stroke="#fff" stroke-width="1.3"/><circle cx="17" cy="12" r="5.5" fill="none" stroke="#fff" stroke-width="1.3"/></svg><p class="suitability__label">Für Kinder ab 4 Jahre</p></div>
    <div class="brand-name"><span class="brand-name__dot"></span>Vanta Prime</div>
    <div class="certification-badge"></div>
    <h1 class="product-title">HYDRATION <span class="product-title__accent">BOOSTER</span></h1>
    <p class="product-subtitle">PREMIUM ISOTONIC ELECTROLYTE DRINK</p>
    <div class="claim-ribbon"></div>
    <p class="claim-ribbon__text">• REFRESH • REPLENISH • RECHARGE!</p>
    <div class="fruit-illustration" role="img" aria-label="Whole orange with a leaf and an orange wedge"></div>
    <div class="stick-count"><span class="stick-count__number">20</span><span class="stick-count__unit">STICKS</span></div>
    <div class="stick-illustration" role="img" aria-label="Product stick tilted over the glass"></div>
    <div class="serving-illustration" role="img" aria-label="Orange powder pouring into a glass of water"></div>
    <p class="flavor-name">ORANGE FLAVOR<span class="flavor-name__note">NATURAL FLAVOR</span></p>
    <p class="free-from">NO ARTIFICIAL COLORS, FLAVORS, OR SWEETENERS</p>
    <div class="diet-marks">
      <div class="diet-mark"><div class="diet-mark__icon"></div><p class="diet-mark__label">Vegan</p></div>
      <div class="diet-mark"><div class="diet-mark__icon"></div><p class="diet-mark__label">Glutenfrei</p></div>
      <div class="diet-mark"><div class="diet-mark__icon"></div><p class="diet-mark__label">Laktosefrei</p></div>
    </div>
    <p class="net-weight">NET WT. 400G (14.11 Oz)</p>
  </article>
</section>

</body>
</html>
```